Simplified minimalist but bold website

Design a website for a brand 'Brighten Every Day' that shares ideas to make managing home and health easier through email swap series, webinars and eventually courses.

Simple landing page to attract users to sign up for a freebie.

Target Market(s)

women with families & homes to run

Number of Pages Required

1 page

Font styles to use
Sans Serif

Colors
e667a6
b768aa
acd136
ffffff
959595

Requirements
Must have
• Simplified look, line icons, opt-in template, contact us form

```html
<!DOCTYPE html>
<html lang="en">
<head>
<meta charset="utf-8">
<title>Brighten Every Day</title>
<link href="https://fonts.googleapis.com/css2?family=Poppins:wght@400;500;600;700&display=swap" rel="stylesheet">
<style>
:root{
  --pink:#e667a6;
  --blue:#2fa3d9;
  --white:#ffffff;
  --grey:#959595;
  --ink:#121212;
  --field-line:#9a9a9a;
}
*{margin:0;padding:0;box-sizing:border-box}
html,body{width:1200px;height:2483px;overflow:hidden}
body{font-family:'Poppins',sans-serif;color:var(--white);background:var(--ink);position:relative}
.section{position:absolute;left:0;width:1200px;overflow:hidden}
.abs{position:absolute}
.center{text-align:center}

/* hero */
.hero{top:0;height:601px}
.hero-photo{position:absolute;inset:0;background:linear-gradient(180deg,#3a5a93 0%,#2c477a 45%,#43464f 75%,#5a5650 100%)}
.hero-shade{position:absolute;inset:0;background:rgba(10,20,45,.25)}
.menu-btn{left:1049px;top:48px;width:26px;height:26px;border-radius:50%;background:var(--white);display:flex;flex-direction:column;justify-content:center;align-items:center;gap:3px}
.menu-btn span{display:block;width:13px;height:2px;background:#2c477a}
.hero-title{left:0;width:1200px;top:208px;font-size:54px;font-weight:600;letter-spacing:-.5px}
.hero-sub{left:0;width:1200px;top:288px;font-size:27px;font-weight:500}
.pill{display:flex;align-items:center;justify-content:center;border-radius:40px;font-weight:500}
.hero-cta{left:534px;top:346px;width:132px;height:43px;background:var(--pink);font-size:15px}

/* opt-in bands */
.band-blue{top:601px;height:490px;background:var(--blue)}
.band-pink{top:1091px;height:491px;background:var(--pink)}
.band-title{left:0;width:1200px;font-size:24px;font-weight:500}
.col-title{font-size:27px;font-weight:600}
.lead{font-size:15.5px;font-weight:500}
.body-lines{font-size:14.5px;line-height:25.5px}
.btn-white{background:var(--white);font-size:15px;height:46px}
.card{background:var(--white)}
.field{position:absolute;height:58px;border:2px solid var(--field-line);border-radius:40px;color:#555;font-size:18px;display:flex;align-items:center;justify-content:center;background:var(--white)}
.submit{position:absolute;height:59px;border-radius:40px;color:var(--white);font-size:18px;font-weight:600;display:flex;align-items:center;justify-content:center}
.guide-art{left:728px;top:197px;width:240px;height:168px;background:linear-gradient(135deg,#eaf3fb 0%,#cfe3f2 50%,#3a8fcf 100%);border-radius:4px}

/* feature */
.feature{top:1582px;height:557px}
.feature-photo{position:absolute;inset:0;background:linear-gradient(100deg,#4e5a5e 0%,#5f8f93 40%,#7ec4c7 70%,#5d8d90 100%)}
.feature-shade{position:absolute;inset:0;background:rgba(30,35,40,.35)}
.feature-title{left:111px;top:65px;font-size:40px;font-weight:600}
.feature-copy{left:113px;top:122px;width:520px;font-size:15px;line-height:25.5px;font-weight:500}
.feature-copy p{margin-bottom:13px}
.feature-cta{left:111px;top:434px;width:427px;height:59px;background:var(--blue);font-size:16px;font-weight:600}

/* footer */
.footer{top:2139px;height:344px;background:var(--ink)}
.foot-head{top:48px;font-size:19px;font-weight:500}
.foot-text{font-size:13.5px;line-height:26px}
.foot-list{list-style:none;font-size:13.5px;line-height:25.7px}
.social{top:211px;left:112px;display:flex;gap:22px}
.social span{width:28px;height:28px;border-radius:50%;background:var(--white);display:block}
.copyright{left:0;width:1200px;top:298px;font-size:13px}
</style>
</head>
<body>

<header class="section hero">
  <div class="hero-photo" role="img" aria-label="Photo of a tidy living room with a navy sofa, cushions, wooden coffee table and framed prints on a blue wall"></div>
  <div class="hero-shade"></div>
  <div class="abs menu-btn" aria-label="Menu"><span></span><span></span><span></span></div>
  <h1 class="abs hero-title center">Brighten Every Day.</h1>
  <p class="abs hero-sub center">Chances are Life is a Little Overwhelming</p>
  <a class="abs pill hero-cta">Let Us Help</a>
</header>

<section class="section band-blue">
  <h2 class="abs band-title center" style="top:43px">Baby Steps... (try out a few of our tricks)</h2>
  <div class="abs center" style="left:99px;width:500px;top:153px">
    <h3 class="col-title">Swaps Email Series</h3>
    <p class="lead" style="margin-top:9px">Save TIME, MONEY and SANITY with simple product swaps.</p>
    <p class="body-lines" style="margin-top:14px">Reduce the amount of work it takes to run your home.<br>Swap out existing products for more sustainable ones.<br>Each swap saves you work, clutter, time &amp; money.</p>
  </div>
  <a class="abs pill btn-white" style="left:179px;top:352px;width:172px;color:var(--blue)">See Sample Swap</a>
  <a class="abs pill btn-white" style="left:359px;top:352px;width:154px;color:var(--blue)">Learn More</a>
  <form class="abs card" style="left:629px;top:122px;width:458px;height:316px">
    <div class="field" style="left:36px;top:55px;width:386px">Name</div>
    <div class="field" style="left:36px;top:124px;width:386px">Email</div>
    <div class="submit" style="left:36px;top:201px;width:386px;background:var(--blue)">Sign Me Up!</div>
  </form>
</section>

<section class="section band-pink">
  <h2 class="abs band-title center" style="top:43px">Big Leap... (I'm ready to roll up my sleeves)</h2>
  <form class="abs card" style="left:111px;top:122px;width:460px;height:316px">
    <div class="field" style="left:38px;top:55px;width:384px">Name</div>
    <div class="field" style="left:38px;top:124px;width:384px">Email</div>
    <div class="submit" style="left:38px;top:200px;width:384px;background:var(--pink)">Send Me The Guide!</div>
  </form>
  <h3 class="abs col-title center" style="left:656px;width:400px;top:136px">Decluttering Guide</h3>
  <div class="abs guide-art" role="img" aria-label="Illustrated covers of the decluttering guide and a user manual booklet"></div>
  <a class="abs pill btn-white" style="left:771px;top:390px;width:154px;color:var(--pink)">Learn More</a>
</section>

<section class="section feature">
  <div class="feature-photo" role="img" aria-label="Wide-angle photo of a bright teal hallway with a white bench, coat hooks and a striped rainbow rug"></div>
  <div class="feature-shade"></div>
  <h2 class="abs feature-title">Swaps Email Series</h2>
  <div class="abs feature-copy">
    <p>Save TIME, MONEY and SANITY with simple product swaps. And reduce the amount of work it takes to run your home. Swap out existing products for more convenient ones. Each swap save you work, clutter, time &amp; money.</p>
    <p>You get an email 2x weekly for 6-12 weeks only Get even more if you feel they are helpful to you</p>
    <p>Join our monthly SIMPLE SWAP SHARING web jams with other mums and get even more ideas. Better yet, come with great tips of your own to share.</p>
  </div>
  <a class="abs pill feature-cta">Sign Me Up</a>
</section>

<footer class="section footer">
  <h4 class="abs foot-head" style="left:116px">About Us</h4>
  <p class="abs foot-text" style="left:112px;top:112px;width:230px">Lorem ipsum dolor sit amet, consectetur adipiscing elit, sed do eiusmod tempor</p>
  <div class="abs social" aria-label="Social links"><span></span><span></span><span></span><span></span></div>

  <h4 class="abs foot-head" style="left:425px">Quick Links</h4>
  <ul class="abs foot-list" style="left:425px;top:106px">
    <li>Home</li><li>About Us</li><li>Services</li><li>Testimonials</li><li>Blog</li><li>Contact Us</li>
  </ul>

  <h4 class="abs foot-head" style="left:617px">Other Services</h4>
  <ul class="abs foot-list" style="left:628px;top:106px">
    <li>Sign Up</li><li>Privacy Policy</li><li>Terms &amp; Conditions</li>
  </ul>

  <h4 class="abs foot-head" style="left:869px">Contact Us</h4>
  <p class="abs foot-text" style="left:872px;top:106px;width:200px;line-height:21px"><span style="font-weight:500">Address:</span> #10,Sed ut perspiciatis unde omnis iste Maplewood</p>
  <p class="abs foot-text" style="left:872px;top:186px">Phone: +1 555 014 2288</p>
  <p class="abs foot-text" style="left:872px;top:226px">Email: hello@brighteneveryday.com</p>

  <p class="abs copyright center">© 2018 Copyrights | All Rights Reserved</p>
</footer>

</body>
</html>
```